Im want a website LIKE VRX's and FleetHollow.com's with product payment options like Trenzo's

I need a website LIKE VRX with a header made EXACTLY LIKE THAT OF FLEETHOLLOWS .

The front page photo should be like that of FLEETHOLLOW's webpage as well.

The name of the website will be called "M.K. (Caldera Key)".

We will be targeting ALL MARKETS in a small town in central Panama and charging businesses "listing fees" like a phone book does but also providing informational blogs, news, and other interesting activities.

THIS IS A MULTI PAGE WEBSITE

THIS IS WHERE VRX's website meets Brivelle/FleetHollow.

Once the layout is built I will tweak and modify, add information, and upload items for sale.

Here is a list of specific categories that should be listed out above the front page header image/search bar

-- Home -- News -- Travel -- Activities -- Shop & Dine -- Store -- More... --

These categories should be spread across the bottom of the page in three sections:

WHATS SO GREAT ABOUT (Caldera Key),
HAND PICKED TOURS
ACTIVITIES etc.

Also lets use www.Trenzo.example 's
"HOT DESTINATIONS"
"BEAT THE BEST PRICES IN BOQUETE"
"OCTOBERS INSIDER PICKS"
"TOP DESTINATIONS"
and spread them in four sections side-by-side near the bottom of the page.

Overall I would like to see the finished product to be something LIKE VRX's and FleetHollows.

WE NEED ONLINE PAYMENT OPTIONS LIKE BRIVELLE'S WEBSITE HAS

This will be a desktop website but should be very mobile friendly as well.

-rodmund

P.S. Good luck!

If it isn't already too late to change the website name, the name of the website should be "Caldera Key". Added Friday, October 9, 2015

What do you guys think the budget should be to win this? Added Saturday, October 10, 2015

www.palmorra.example is the most amazing simple site. Whoever can make me a replica with my specifications will win immediately!!!! Added Sunday, October 18, 2015

OMG www.palmorra.example is the bomb!So simple and elegant. Whoever can make me an EXACT REPLICA OF WWW.PALMORRA.EXAMPLE as my site with the specifications mentioned in my brief will take home the $825.00 immediately! Good luck amigos! Added Sunday, October 18, 2015

Does anybody know how to add recurring monthly billing options on this website? Added Sunday, October 18, 2015

ALL MARKETS

Product

Coded - Design and coding required

5+ page

• Coinvey payment options.
• I must be able to add and remove photos/text and video from the HTML files in the page.
• Be creative my friends, and may the odds be forever in your favor!
• I added some photos of a good layout for our page below.

```html
<!DOCTYPE html>
<html lang="en">
<head>
<meta charset="utf-8">
<title>Caldera Key</title>
<link href="https://fonts.googleapis.com/css2?family=Open+Sans:wght@400;600;700&family=Raleway:wght@400;600;700&display=swap" rel="stylesheet">
<style>
:root{
  --navy:#0e3553;
  --navy-deep:#0b2a43;
  --navy-band:#103b5e;
  --navy-bottom:#092236;
  --accent:#2f80c2;
  --ink:#333d45;
  --muted:#7b858c;
  --btn-gray:#8e959a;
  --btn-light:#6d8aa3;
  --icon-bg:#e6e9eb;
  --foot-text:#c2cfd9;
  --gold:#f2b01e;
  --white:#ffffff;
}
*{box-sizing:border-box;margin:0;padding:0}
html,body{width:684px;height:1200px;overflow:hidden}
body{font-family:"Open Sans",Arial,sans-serif;color:var(--ink);background:var(--white);position:relative;font-size:7px;line-height:1.55}
.wrap{width:504px;margin:0 auto;position:relative}

/* hero */
.hero{position:relative;height:328px}
.hero-bg{position:absolute;inset:0 0 auto 0;height:326px;background:linear-gradient(180deg,#4d8bb8 0%,#8fbfd8 35%,#cfd9cf 62%,#e9dcc0 100%)}
.topbar{position:relative;height:72px;display:flex;justify-content:space-between;align-items:center}
.brand{font-family:"Raleway",sans-serif;font-weight:600;font-size:15px;color:var(--white)}
.top-actions{display:flex;gap:6px}
.top-actions span{background:var(--white);color:var(--ink);font-size:7px;padding:4px 8px;border-radius:2px}
.slider{position:relative;height:256px;background:linear-gradient(160deg,#f4c35a 0%,#e59a3b 30%,#5f90b8 65%,#2f5f86 100%)}
.slider h2{position:absolute;right:24px;top:106px;font-family:"Raleway",sans-serif;font-weight:600;font-size:22px;color:var(--white)}
.dots{position:absolute;bottom:10px;left:50%;transform:translateX(-50%);display:flex;gap:5px}
.dots i{width:6px;height:6px;border-radius:50%;background:rgba(255,255,255,.55)}
.dots i:first-child{background:var(--white)}
.promo{height:54px;background:var(--navy);display:flex;align-items:center;justify-content:space-between;padding:0 26px 0 50px}
.promo p{font-family:"Raleway",sans-serif;font-weight:700;font-size:16px;color:var(--white)}
.btn{display:inline-block;font-size:7px;font-weight:600;text-transform:uppercase;letter-spacing:.5px;padding:6px 14px;color:var(--white)}
.btn-light{background:var(--btn-light)}
.btn-gray{background:var(--btn-gray)}
.btn-navy{background:var(--navy);border:1px solid rgba(255,255,255,.4)}

/* welcome */
.welcome{text-align:center;padding-top:30px;height:184px}
.section-title{font-family:"Raleway",sans-serif;font-weight:600;font-size:16px;color:var(--ink);margin-bottom:10px}
.welcome p{color:var(--muted);width:440px;margin:0 auto 12px}

/* features */
.features{display:flex;justify-content:space-between;height:130px}
.feature{width:152px}
.feature-head{display:flex;align-items:center;gap:10px;margin-bottom:10px}
.feature-icon{width:42px;height:36px;background:var(--icon-bg);display:flex;align-items:center;justify-content:center;flex:none}
.feature h3{font-size:8px;font-weight:700;color:var(--accent);text-transform:uppercase;line-height:1.3}
.feature p{color:var(--muted)}

/* tours */
.tours{text-align:center;height:224px}
.tours .sub{color:var(--muted);font-size:8px;margin-top:-4px;margin-bottom:12px}
.cards{display:flex;justify-content:space-between;text-align:left}
.card{width:158px}
.card-img{position:relative;height:104px}
.card:nth-child(1) .card-img{background:linear-gradient(170deg,#8ab4d8,#b58e6b 60%,#7a6b5a)}
.card:nth-child(2) .card-img{background:linear-gradient(170deg,#2d3a4a,#6a7f93 55%,#c9a97a)}
.card:nth-child(3) .card-img{background:linear-gradient(170deg,#f0d9a8,#c47a3d 55%,#6b3a1f)}
.card-meta{position:absolute;left:0;right:0;bottom:0;height:20px;background:rgba(10,30,48,.75);color:var(--white);display:flex;align-items:center;justify-content:space-between;padding:0 7px;font-size:6px}
.card-meta b{font-size:10px;font-weight:600}
.card h4{font-family:"Raleway",sans-serif;font-weight:600;font-size:11px;margin-top:6px;color:var(--ink)}
.stars{color:var(--gold);font-size:9px;letter-spacing:1px;line-height:1.2}

/* tweet band */
.tweet{background:var(--navy-band);height:72px;color:var(--white)}
.tweet .wrap{height:72px;display:flex;align-items:center;gap:12px}
.tweet-dot{width:20px;height:20px;border-radius:50%;background:var(--accent);flex:none}
.tweet p{flex:1;font-size:7px;line-height:1.7}
.tweet small{display:block;color:#a9bccb;font-size:6px}
.arrows{display:flex;gap:4px}
.arrows span{width:16px;height:16px;background:var(--white);color:var(--navy);display:flex;align-items:center;justify-content:center;font-size:9px;font-weight:700}

/* footer */
.footer{background:var(--navy-deep);height:178px;color:var(--foot-text)}
.footer .wrap{display:flex;justify-content:space-between;padding-top:18px}
.col h5{font-family:"Raleway",sans-serif;font-weight:700;font-size:9px;color:var(--white);margin-bottom:7px}
.col li{list-style:none;font-size:6.5px;line-height:1.8}
.col-about{width:130px}
.col-about p{font-size:6.5px;margin-bottom:9px}
.col-news{width:130px}
.col-news p{font-size:6.5px;margin-bottom:6px}
.field{height:16px;background:var(--white);margin-bottom:8px;color:#9aa3aa;font-size:6px;padding:3px 6px}
.news-row{display:flex;align-items:center;gap:8px}
.social{display:flex;gap:5px}
.social i{width:10px;height:10px;border-radius:50%;background:var(--foot-text)}
.bottombar{background:var(--navy-bottom);height:30px;color:#8fa3b3;font-size:6.5px}
.bottombar .wrap{height:30px;display:flex;align-items:center;justify-content:center}
.bottombar .top{position:absolute;right:0}
</style>
</head>
<body>

<section class="hero">
  <div class="hero-bg" role="img" aria-label="Beach with palm trees behind the header"></div>
  <div class="wrap">
    <header class="topbar">
      <span class="brand">Caldera Key</span>
      <div class="top-actions"><span>Sign | Login</span><span>$</span></div>
    </header>
    <div class="slider" role="img" aria-label="Sunlit city landmark tower for the guided tours slide">
      <h2>Selling guided tours</h2>
      <div class="dots"><i></i><i></i><i></i></div>
    </div>
  </div>
</section>

<div class="wrap">
  <div class="promo">
    <p>Discover our Top tours from $34</p>
    <span class="btn btn-light">Read more</span>
  </div>
</div>

<main class="wrap">
  <section class="welcome">
    <h2 class="section-title">Welcome to Caldera Key</h2>
    <p>Lorem Ipsum is simply dummy text of the printing and typesetting industry. Lorem Ipsum has been the industry's standard dummy text ever since the 1500s, when an unknown printer took a galley of type and scrambled it to make a type specimen book. It has survived not only five centuries, but also the leap into electronic typesetting remaining essentially unchanged.</p>
    <span class="btn btn-gray">Read more</span>
  </section>

  <section class="features">
    <div class="feature">
      <div class="feature-head">
        <div class="feature-icon"><svg width="22" height="22" viewBox="0 0 24 24"><path fill="#2f80c2" d="M21 16v-2l-8-5V3.5a1.5 1.5 0 0 0-3 0V9l-8 5v2l8-2.5V19l-2 1.5V22l3.5-1 3.5 1v-1.5L13 19v-5.5z"/></svg></div>
        <h3>Selling guided<br>tours</h3>
      </div>
      <p>Lorem Ipsum is simply dummy text of the printing and typesetting industry. Lorem Ipsum has been the industry's standard dummy text ever since the 1500s.</p>
    </div>
    <div class="feature">
      <div class="feature-head">
        <div class="feature-icon"><svg width="22" height="22" viewBox="0 0 24 24"><rect x="4" y="3" width="16" height="19" fill="#2f80c2"/><g fill="#fff"><rect x="7" y="6" width="3" height="3"/><rect x="14" y="6" width="3" height="3"/><rect x="7" y="11" width="3" height="3"/><rect x="14" y="11" width="3" height="3"/><rect x="10.5" y="17" width="3" height="5"/></g></svg></div>
        <h3>Hostels</h3>
      </div>
      <p>Lorem Ipsum is simply dummy text of the printing and typesetting industry. Lorem Ipsum has been the industry's standard dummy text ever since the 1500s.</p>
    </div>
    <div class="feature">
      <div class="feature-head">
        <div class="feature-icon"><svg width="24" height="22" viewBox="0 0 26 24"><path fill="#2f80c2" d="M4 11l2.5-6h13L22 11h1v7h-2v2h-3v-2H8v2H5v-2H3v-7zm3.5-4L6 11h14l-1.5-4z"/><circle cx="7" cy="14.5" r="1.5" fill="#fff"/><circle cx="19" cy="14.5" r="1.5" fill="#fff"/></svg></div>
        <h3>Rental vehicles</h3>
      </div>
      <p>Lorem Ipsum is simply dummy text of the printing and typesetting industry. Lorem Ipsum has been the industry's standard dummy text ever since the 1500s.</p>
    </div>
  </section>

  <section class="tours">
    <h2 class="section-title">Top Tours &amp; Rental Vehicles</h2>
    <p class="sub">Lorem Ipsum is simply dummy text of the printing and typesetting industry...</p>
    <div class="cards">
      <article class="card">
        <div class="card-img" role="img" aria-label="Historic stone amphitheatre under a blue sky">
          <div class="card-meta"><span>Hotel &nbsp; 2 days ago</span><b>$ 45</b></div>
        </div>
        <h4>Lorem Ipsum Hotel</h4>
        <div class="stars">★★★★☆</div>
      </article>
      <article class="card">
        <div class="card-img" role="img" aria-label="Hotel room interior at dusk">
          <div class="card-meta"><span>Hotel &nbsp; 3 days ago</span><b>$ 45</b></div>
        </div>
        <h4>Lorem Ipsum Hotel</h4>
        <div class="stars">★★★★☆</div>
      </article>
      <article class="card">
        <div class="card-img" role="img" aria-label="Warmly lit hotel lobby">
          <div class="card-meta"><span>Hotel &nbsp; 5 days ago</span><b>$ 45</b></div>
        </div>
        <h4>Lorem Ipsum Hotel</h4>
        <div class="stars">★★★★☆</div>
      </article>
    </div>
  </section>
</main>

<section class="tweet">
  <div class="wrap">
    <span class="tweet-dot"></span>
    <p>RT @StudioLedger "Working on the right thing is probably more important than working hard"<br>- Marisol Venn Pixmote Founder<small>198 days ago</small></p>
    <div class="arrows"><span>&lsaquo;</span><span>&rsaquo;</span></div>
  </div>
</section>

<footer class="footer">
  <div class="wrap">
    <div class="col col-about">
      <h5>Caldera Key</h5>
      <p>Lorem Ipsum is simply dummy text of the printing and typesetting industry. Lorem Ipsum has been the industry's standard dummy text ever since the 1500s.</p>
      <span class="btn btn-navy">Manage projects</span>
    </div>
    <div class="col">
      <h5>Support</h5>
      <ul><li>Customer Care</li><li>Privacy Policy</li><li>List Your Business</li><li>Group Services</li><li>Manage Projects</li></ul>
    </div>
    <div class="col">
      <h5>Partnerships</h5>
      <ul><li>Work With Us</li><li>Supplier Sign Up</li><li>Destination Programs</li><li>Travel Agents</li></ul>
    </div>
    <div class="col col-news">
      <h5>Newsletter Sign Up</h5>
      <p>Please sign up for our latest news.</p>
      <div class="field">Your email</div>
      <div class="news-row">
        <span class="btn btn-navy">Subscribe</span>
        <div class="social"><i></i><i></i><i></i></div>
      </div>
    </div>
  </div>
</footer>

<div class="bottombar">
  <div class="wrap">
    <span>© 2015 Caldera Key. All right reserved. Term of Use</span>
    <span class="top">TOP</span>
  </div>
</div>

</body>
</html>
```